Business Card Design (NEW FILES)

ATTENTION: New vector files are available. Please update your design to reflect/use the new (better resolution) logo images.

Seeking a unique and professional business card design for a commercial drone photography/videography business. The layout should feature
the logo (attached) and include the following information:
Owen Tarrick
614-502-7738
www.skylarkreelworks.example
NRD Certified Remote Pilot

Owen Tarrick

```html
<!DOCTYPE html>
<html lang="en">
<head>
<meta charset="utf-8">
<title>Owen Tarrick – Business Card</title>
<link rel="stylesheet" href="https://fonts.googleapis.com/css2?family=Open+Sans:ital,wght@0,400;0,600;0,700;1,400&display=swap">
<style>
  :root {
    --backdrop: #232323;
    --navy: #111640;
    --navy-deep: #0d1236;
    --navy-soft: #1e2450;
    --pattern-blue: #2a3a8c;
    --copper: #e07b3c;
    --white: #ffffff;
    --muted: #c9cbe0;
  }
  * { box-sizing: border-box; margin: 0; padding: 0; }
  html, body { width: 1200px; height: 780px; overflow: hidden; }
  body {
    background: var(--backdrop);
    font-family: "Open Sans", Arial, sans-serif;
    display: flex;
    align-items: center;
    justify-content: center;
    gap: 40px;
  }
  .card {
    position: relative;
    width: 540px;
    height: 330px;
    border-radius: 22px;
    background: var(--navy);
    border: 4px solid var(--copper);
    overflow: hidden;
  }
  /* front */
  .drone-art {
    position: absolute;
    left: 130px; top: 40px;
    width: 360px; height: 250px;
    border-radius: 50%;
    background: radial-gradient(ellipse at center, var(--navy-soft) 0%, rgba(30,36,80,0.5) 45%, rgba(17,22,64,0) 72%);
  }
  .accent-line {
    position: absolute;
    left: 0; top: 0;
    width: 532px; height: 322px;
  }
  .name {
    position: absolute;
    left: 52px; top: 70px;
    font-size: 34px;
    font-weight: 700;
    letter-spacing: -0.5px;
    line-height: 1.2;
    color: var(--white);
  }
  .name .first { color: var(--copper); }
  .role {
    position: absolute;
    left: 178px; top: 116px;
    font-size: 15px;
    font-style: italic;
    color: var(--white);
  }
  .contact {
    position: absolute;
    left: 256px; top: 170px;
    list-style: none;
    color: var(--white);
    font-size: 15px;
    font-weight: 600;
    white-space: nowrap;
  }
  .contact li { display: flex; align-items: center; gap: 8px; margin-bottom: 6px; }
  .contact svg { width: 15px; height: 15px; flex: none; }
  .credential {
    position: absolute;
    left: 52px; bottom: 40px;
    font-size: 15px;
    font-weight: 600;
    color: var(--muted);
  }
  /* back */
  .pattern {
    position: absolute;
    inset: 0;
    background: linear-gradient(135deg, var(--navy-deep) 0%, #1a2262 55%, var(--pattern-blue) 100%);
  }
  .brand {
    position: absolute;
    right: 34px; bottom: 34px;
    display: flex;
    align-items: center;
    gap: 8px;
    font-size: 18px;
    font-weight: 600;
    letter-spacing: 1px;
    color: var(--white);
  }
  .brand-dot {
    width: 12px; height: 12px;
    border-radius: 50%;
    background: var(--copper);
  }
</style>
</head>
<body>
  <section class="card card-front">
    <div class="drone-art" role="img" aria-label="Faint drone illustration with camera lens"></div>
    <svg class="accent-line" viewBox="0 0 532 322" aria-hidden="true">
      <line x1="300" y1="112" x2="220" y2="186" stroke="var(--copper)" stroke-width="1.2" opacity="0.8"/>
    </svg>
    <h1 class="name"><span class="first">Owen</span> Tarrick</h1>
    <p class="role">Owner</p>
    <ul class="contact">
      <li>
        <svg viewBox="0 0 16 16" aria-hidden="true"><path fill="var(--copper)" d="M3.6 1.5l2.3 2.4-1.3 1.9c.8 1.8 2.2 3.2 4 4l1.9-1.3 2.4 2.3-1.4 2.2C6.8 12.6 3.4 9.2 1.4 4z"/></svg>
        614-502-7738
      </li>
      <li>
        <svg viewBox="0 0 16 16" aria-hidden="true"><circle cx="8" cy="8" r="7" fill="var(--copper)"/><path d="M1 8h14M8 1c2.4 2 2.4 12 0 14M8 1c-2.4 2-2.4 12 0 14" stroke="var(--navy)" stroke-width="1" fill="none"/></svg>
        www.skylarkreelworks.example
      </li>
    </ul>
    <p class="credential">NRD Certified Remote Pilot, Fully Insured</p>
  </section>

  <section class="card card-back">
    <div class="pattern" role="img" aria-label="Repeating embossed drone pattern"></div>
    <div class="brand"><span class="brand-dot"></span>SKYLARK REELWORKS</div>
  </section>
</body>
</html>
```